New Business Card Design for Manufacturing

We are an engineering/manufacturing company that offers Advanced machining/assembly/engineering services, as well as innovative products for the heavy duty engine cooling markets.

We are looking to get a new business card designed that is clean and modern looking, but still fits the wide range of technical/skilled work we do.

- We hope to use this design as the base for other design work in new Presentations, web, and print work.

Industry/Entity Type

Engineering

Contact Information for Business Card

Our preferred color of blue is (RGB) 22/71/159 but can vary slightly from that color. Our content will be our Logo and full company name (Vantrell Forge Works, Inc.), company address, name, job title, phone number with extension, cell number, fax number, website, and email address on the cards.
We'd like the full company name next to the logo, but we are open to other interpretations of that layout.
Preferably, we would like the back side to be clean with just our logo, and the front to contain all of the contact information.

Colors
2f74b4
0355a3
85abd2

Requirements
Must have
• - Logo, company name, needed content - We are open to interpretation beyond that.
• - Standard size business card.
• - Horizontal orientation.
• - Enough space for lengthy names / job titles (for example, a job title could read "Directory of Human Resources" or "V.P. of Governmental Affairs"). We need this to look clean, whether the title be short (CEO) or long (as described above).

```html
<!DOCTYPE html>
<html lang="en">
<head>
<meta charset="utf-8">
<title>Vantrell Forge Works – Business Card</title>
<link rel="stylesheet" href="https://fonts.googleapis.com/css2?family=Lato:wght@400;700;900&display=swap">
<style>
  :root {
    --brand-blue: #0f5fbf;
    --brand-blue-deep: #0355a3;
    --brand-blue-mid: #2f74b4;
    --steel: #a9bed8;
    --steel-deep: #85abd2;
    --paper: #f7f8f9;
    --ink-white: #ffffff;
    --backdrop: #e6e9ee;
  }
  * { box-sizing: border-box; margin: 0; padding: 0; }
  html, body { width: 1200px; height: 780px; overflow: hidden; }
  body {
    background: var(--backdrop);
    font-family: "Lato", Arial, sans-serif;
    display: flex;
    align-items: center;
    justify-content: center;
    gap: 26px;
  }
  .card {
    width: 560px;
    height: 320px;
    position: relative;
    overflow: hidden;
    border-radius: 3px;
    box-shadow: 0 6px 18px rgba(20, 40, 80, 0.18);
  }

  /* Front */
  .card-front { display: flex; flex-direction: column; }
  .front-brand {
    height: 140px;
    background: var(--paper);
    display: flex;
    align-items: center;
    padding-left: 44px;
    gap: 18px;
  }
  .brand-square {
    width: 58px; height: 58px;
    background: var(--brand-blue);
  }
  .brand-name {
    color: var(--brand-blue);
    font-weight: 900;
    font-size: 21px;
    line-height: 1.02;
    text-transform: uppercase;
    letter-spacing: 0.5px;
  }
  .front-contact {
    height: 135px;
    background: linear-gradient(90deg, var(--brand-blue-deep), var(--brand-blue) 55%, var(--brand-blue-mid));
    color: var(--ink-white);
    display: flex;
    align-items: center;
    padding: 0 28px 0 44px;
  }
  .person { width: 215px; }
  .person-name { font-weight: 900; font-size: 17px; text-transform: uppercase; letter-spacing: 0.3px; }
  .person-title { font-size: 13px; margin-top: 1px; }
  .person-address { font-size: 13px; margin-top: 12px; line-height: 1.35; }
  .divider { width: 1px; height: 84px; background: rgba(255,255,255,0.75); margin-right: 16px; }
  .contact-list { list-style: none; font-size: 13px; }
  .contact-list li { display: flex; align-items: center; gap: 8px; line-height: 21px; }
  .contact-icon { width: 14px; height: 14px; flex: none; }
  .steel-band {
    flex: 1;
    background: linear-gradient(180deg, var(--steel), var(--steel-deep));
  }

  /* Back */
  .card-back {
    background: radial-gradient(ellipse at 50% 40%, #1b6fd0, var(--brand-blue-deep) 85%);
  }
  .back-brand {
    position: absolute;
    left: 0; right: 0; top: 0; bottom: 46px;
    display: flex;
    align-items: center;
    justify-content: center;
    gap: 20px;
  }
  .back-brand .brand-square { background: var(--ink-white); width: 66px; height: 66px; }
  .back-brand .brand-name { color: var(--ink-white); font-size: 24px; }
  .back-band {
    position: absolute;
    left: 0; right: 0; bottom: 0;
    height: 46px;
    background: linear-gradient(180deg, var(--steel), var(--steel-deep));
    display: flex;
    align-items: center;
    justify-content: center;
    color: #eef3f9;
    font-size: 12px;
    letter-spacing: 4px;
  }
</style>
</head>
<body>

  <section class="card card-front" aria-label="Business card front">
    <div class="front-brand">
      <div class="brand-square"></div>
      <div class="brand-name">Vantrell<br>Forge<br>Works, Inc.</div>
    </div>
    <div class="front-contact">
      <div class="person">
        <div class="person-name">Dana Orley</div>
        <div class="person-title">Founder</div>
        <div class="person-address">PO BOX 418 Ridgeline Road<br>2nd floor, Dayton OH</div>
      </div>
      <div class="divider"></div>
      <ul class="contact-list">
        <li>
          <svg class="contact-icon" viewBox="0 0 14 14"><circle cx="7" cy="7" r="7" fill="#fff"/><rect x="4.6" y="3" width="4.8" height="8" rx="0.8" fill="none" stroke="#0f5fbf" stroke-width="1.1"/></svg>
          (555) 014-2270
        </li>
        <li>
          <svg class="contact-icon" viewBox="0 0 14 14"><circle cx="7" cy="7" r="7" fill="#fff"/><path d="M4 4.5c0 3 2.5 5.5 5.5 5.5l0.8-1.4-1.6-0.9-0.8 0.8c-1-0.4-1.8-1.2-2.2-2.2l0.8-0.8-0.9-1.6z" fill="#0f5fbf"/></svg>
          (555) 014-8831
        </li>
        <li>
          <svg class="contact-icon" viewBox="0 0 14 14"><circle cx="7" cy="7" r="7" fill="#fff"/><rect x="3.5" y="4.5" width="7" height="5" fill="none" stroke="#0f5fbf" stroke-width="1"/><path d="M3.5 4.5l3.5 3 3.5-3" fill="none" stroke="#0f5fbf" stroke-width="1"/></svg>
          info@vantrellforge.com
        </li>
        <li>
          <svg class="contact-icon" viewBox="0 0 14 14"><circle cx="7" cy="7" r="7" fill="#fff"/><circle cx="7" cy="7" r="3.8" fill="none" stroke="#0f5fbf" stroke-width="0.9"/><ellipse cx="7" cy="7" rx="1.6" ry="3.8" fill="none" stroke="#0f5fbf" stroke-width="0.9"/><path d="M3.2 7h7.6" stroke="#0f5fbf" stroke-width="0.9"/></svg>
          www.vantrellforge.com
        </li>
      </ul>
    </div>
    <div class="steel-band"></div>
  </section>

  <section class="card card-back" aria-label="Business card back">
    <div class="back-brand">
      <div class="brand-square"></div>
      <div class="brand-name">Vantrell<br>Forge<br>Works, Inc.</div>
    </div>
    <div class="back-band">www.vantrellforge.com</div>
  </section>

</body>
</html>
```